Business cards to launch an education platform

Hi,
I am looking at having new business cards designed.
I am a startup, developing a web platform for schools and university, the education world. It's an online assessment system.
I would like a card that looks classy, and that is using the colors and the font of my logo.

I have attached:
1) my logo
2) A business card that I have designed quickly so you can have all the information required in the card, but I really don't like it.
3) The font that I am using (Lato Regular) to design my web platform
4) Some screenshots of my web platform so you can have a look at the style that I have.

Target Market(s)

Major market: Education system: Schools and university
Minor markets: Business in general

Industry/Entity Type

Business

Contact Information for Business Card

Clara Fenwick
Director

M: 0437 518 902
E: clara.fenwick@amberLoomSystems.com.au

Requirements
Must have
• The colors of my logo

```html
<!DOCTYPE html>
<html lang="en">
<head>
<meta charset="utf-8">
<title>Amber Loom Systems – Business Cards</title>
<link rel="stylesheet" href="https://fonts.googleapis.com/css2?family=Lato:wght@400;700&display=swap">
<style>
  :root {
    --page-bg: #e9e9e9;
    --silver-edge: #c9cbcd;
    --silver-mid: #ffffff;
    --navy: #1f4e86;
    --deep-blue: #1b4a8c;
    --band-top: #2a93c9;
    --band-bottom: #1a4b8b;
    --sky: #2ea6df;
    --ink: #333333;
    --white: #ffffff;
  }
  * { margin: 0; padding: 0; box-sizing: border-box; }
  html, body {
    width: 1107px; height: 1200px; overflow: hidden;
    background: var(--page-bg);
    font-family: "Lato", Arial, sans-serif;
  }
  .canvas { position: relative; width: 1107px; height: 1200px; }

  .card {
    position: absolute; left: 138px; width: 830px; height: 481px;
    background: linear-gradient(90deg, var(--silver-edge) 0%, var(--silver-mid) 45%, var(--silver-mid) 60%, var(--silver-edge) 100%);
    overflow: hidden;
    box-shadow: 0 2px 8px rgba(0,0,0,0.18);
  }
  .card--front { top: 96px; }
  .card--back { top: 655px; }

  .card__band { position: absolute; inset: 0; width: 830px; height: 481px; }

  .card__url {
    position: absolute; left: 0; right: 0; top: 382px;
    text-align: center; color: var(--white);
    font-weight: 700; font-size: 28px;
  }

  .brand { position: absolute; display: flex; align-items: center; }
  .brand__mark { background: var(--deep-blue); flex: none; }
  .brand__name {
    color: var(--navy); font-weight: 400; line-height: 1.1;
  }
  .brand__line { display: block; }
  .brand__line--upper { text-transform: uppercase; letter-spacing: 0.06em; }
  .brand__line--lower { letter-spacing: 0.08em; }

  .brand--large { left: 108px; top: 70px; }
  .brand--large .brand__mark { width: 180px; height: 180px; margin-right: 36px; }
  .brand--large .brand__name { font-size: 54px; }

  .brand--small { left: 510px; top: 44px; }
  .brand--small .brand__mark { width: 98px; height: 98px; margin-right: 14px; }
  .brand--small .brand__name { font-size: 30px; }

  .contact { position: absolute; left: 129px; top: 128px; color: var(--ink); }
  .contact__name { font-weight: 700; font-size: 25px; }
  .contact__role { font-size: 24px; margin-top: 2px; }
  .contact__list { list-style: none; margin-top: 24px; }
  .contact__item { display: flex; align-items: center; font-size: 24px; height: 36px; }
  .contact__icon { width: 22px; height: 22px; margin-right: 8px; flex: none; }
</style>
</head>
<body>
<main class="canvas">

  <section class="card card--front" aria-label="Card front">
    <svg class="card__band" viewBox="0 0 830 481" aria-hidden="true">
      <defs>
        <linearGradient id="bandFront" x1="0" y1="0" x2="0" y2="1">
          <stop offset="0" stop-color="#2a93c9"/>
          <stop offset="1" stop-color="#1a4b8b"/>
        </linearGradient>
        <linearGradient id="rimFront" x1="0" y1="0" x2="1" y2="0">
          <stop offset="0" stop-color="#9a9ca0"/>
          <stop offset="0.5" stop-color="#f4f4f4"/>
          <stop offset="1" stop-color="#8f9296"/>
        </linearGradient>
      </defs>
      <path d="M0 330 Q415 292 830 340 L830 481 L0 481 Z" fill="url(#rimFront)"/>
      <path d="M0 338 Q415 300 830 348 L830 481 L0 481 Z" fill="url(#bandFront)"/>
    </svg>
    <div class="brand brand--large">
      <span class="brand__mark" aria-hidden="true"></span>
      <span class="brand__name">
        <span class="brand__line brand__line--upper">Amber Loom</span>
        <span class="brand__line brand__line--lower">Systems</span>
      </span>
    </div>
    <p class="card__url">www.amberLoomSystems.com.au</p>
  </section>

  <section class="card card--back" aria-label="Card back">
    <svg class="card__band" viewBox="0 0 830 481" aria-hidden="true">
      <defs>
        <linearGradient id="bandBack" x1="0" y1="0" x2="0" y2="1">
          <stop offset="0" stop-color="#2a93c9"/>
          <stop offset="1" stop-color="#1a4b8b"/>
        </linearGradient>
        <linearGradient id="rimBack" x1="0" y1="0" x2="1" y2="0">
          <stop offset="0" stop-color="#9a9ca0"/>
          <stop offset="0.5" stop-color="#f4f4f4"/>
          <stop offset="1" stop-color="#8f9296"/>
        </linearGradient>
      </defs>
      <path d="M0 330 Q415 292 830 340 L830 481 L0 481 Z" fill="url(#rimBack)"/>
      <path d="M0 338 Q415 300 830 348 L830 481 L0 481 Z" fill="url(#bandBack)"/>
    </svg>
    <div class="brand brand--small">
      <span class="brand__mark" aria-hidden="true"></span>
      <span class="brand__name">
        <span class="brand__line brand__line--upper">Amber Loom</span>
        <span class="brand__line brand__line--lower">Systems</span>
      </span>
    </div>
    <div class="contact">
      <p class="contact__name">Clara Fenwick</p>
      <p class="contact__role">Director</p>
      <ul class="contact__list">
        <li class="contact__item">
          <svg class="contact__icon" viewBox="0 0 22 22" aria-hidden="true">
            <rect x="5" y="1.5" width="12" height="19" rx="2" fill="none" stroke="#1b4a8c" stroke-width="1.6"/>
            <line x1="9" y1="17" x2="13" y2="17" stroke="#1b4a8c" stroke-width="1.4"/>
          </svg>
          0437 518 902
        </li>
        <li class="contact__item">
          <svg class="contact__icon" viewBox="0 0 22 22" aria-hidden="true">
            <rect x="1.5" y="5" width="19" height="13" fill="none" stroke="#1b4a8c" stroke-width="1.6"/>
            <path d="M1.5 5 L11 12.5 L20.5 5" fill="none" stroke="#1b4a8c" stroke-width="1.6"/>
          </svg>
          clara.fenwick@amberLoomSystems.com.au
        </li>
      </ul>
    </div>
    <p class="card__url">www.amberLoomSystems.com.au</p>
  </section>

</main>
</body>
</html>
```